MyName is TapLedger .... Killer of Business Cards!!! WANT a KickAss Design Landing Page :)

How 'TapLedger' works:
- with a unique name for each country, like a personalise car plate number
- our platform links through a 'Quick Text' keyword short code
- TapLedger platform will respond with downloaded ready full contact business file link
- this is designed to be downloaded in just '3 clicks' into your Contacts Folder
- any changes,,updates, images, online profiles can be made in real time updates
- TapLedger provides a backend login to manage individual account and is ready
Enterprise model for larger staff companies
- platform is international ready and have launched
Australia, in September 2019.

Yes, your whole business card and online profile in '3' simple clicks. No '20-30 mins' of typing the business card contacts details into mobile phones.
** Fact: 88% of business cards are lost of thrown out within 7 days.
(https://www.plumfinchstats.com/business-card-statistics.html) **

NZ ClipStream
https://vidhost.example/q7Rt2LmP9xZ

**current websites are www.tapledge.co.nz www.taplink.com.au www.tapledgerau.com www.tapledgerus.com **

Target Market(s)

Anybody who uses a business card, from trades person, real estate agents, consultants, bankers (in NZ/AU with have plumbers, financial advisors, real estate agents, mortgage brokers, sports agents, Telcos etc etc)

Industry/Entity Type

Business Software

Coding

Coded - Design and coding required

Number of Pages Required

4 page

Font styles to use
Other font styles liked:
• libre franklin black

Requirements
Must have
• TapLedger a simple 'in delivery' and smart 'in innovation' solution so our message is Simple, Clear and Inquisitive. We would like a converting landing page because we are selling Nimble Cloud Suite at low-entry cost and no-contract. IWe want to direct clients to a name reservation platform to a virtual business card that uses our Nimble Core Engine. We will require some code at the back to link the name reservation and sign up source code(javascript). This web/landing page fresh page is required because we have recently changed our marketing strategy to be purely digital marketing in Chatterbook and Snapgrid Ads from now on. We would like this to be exciting graphically to grab attention, inquisitive enough to check your name availability and follow through with call to action with the right colours and graphics images. We plan to test the right pitch offering until we get the markets feedback on the best offering/re-design and then push harder with more CB and SG Ads. ( **we plan to continue multiple regular campaigns as the business has now change our strategy due to covid-19 and we will focus mainly on direct to consumers**)

Also:
2 buttons: Signup and a Check availability little form to allow a java script to be added/HTML5/CB advertising/Super Inviting to check 'YOUR UNIQUE NAME' is available. Then clicking the to reserve the name to purchase our Quick Text/Eco-Friendly/Relevant to todays tech and Low Cost service. We will be offering Promo codes for each campaign.
No Apps. Works with SMS, any smartphone, country specific, enterprise ready, and CONTACTLESS ....
Nice to have
• Personal feeling. Unique choice of 'your name' as this is your business and social profile in one. Strong independent images and confident to share with anybody their profile by just sharing their name.
Should not have
• Open currently....

```html
<!DOCTYPE html>
<html lang="en">
<head>
<meta charset="utf-8">
<title>TapLedger – Your Business Card in 3 Clicks</title>
<link rel="stylesheet" href="https://fonts.googleapis.com/css2?family=Libre+Franklin:wght@400;500;600;700;900&display=swap">
<style>
:root{
  --navy:#213a6d;
  --teal:#0f8a8c;
  --teal-bright:#19c2b4;
  --text:#5d6370;
  --ink:#1d2230;
  --grey-band:#f1f2f5;
  --line:#e4e6ea;
  --white:#ffffff;
}
*{box-sizing:border-box;margin:0;padding:0}
html,body{width:1200px;height:3654px;overflow:hidden}
body{position:relative;background:var(--white);font-family:"Libre Franklin",Arial,sans-serif;color:var(--text)}
.abs{position:absolute}
.top-rule{left:0;top:0;width:1200px;height:3px;background:var(--teal)}

/* header */
.brand{left:142px;top:40px;display:flex;align-items:center;gap:12px}
.brand-mark{width:30px;height:30px;border-radius:50%;background:var(--teal)}
.brand-name{font-size:30px;font-weight:700;color:var(--navy);letter-spacing:1px}
.nav{left:460px;top:52px;display:flex;gap:22px;font-size:15px;font-weight:500;color:var(--ink)}
.nav a{color:inherit;text-decoration:none;padding:2px 5px 12px}
.nav a.active{border-bottom:3px solid var(--teal)}
.btn{display:inline-flex;align-items:center;justify-content:center;gap:8px;border-radius:22px;color:var(--white);font-weight:500;font-size:15px;text-decoration:none}
.btn-signup{left:717px;top:41px;width:123px;height:42px;background:var(--teal)}
.btn-check{left:845px;top:41px;width:209px;height:42px;background:var(--navy)}

/* hero */
.hero-title{left:143px;top:205px;font-size:72px;font-weight:500;color:var(--navy);letter-spacing:1px}
.hero-copy{left:146px;top:326px;width:400px;font-size:16px;line-height:30px}
.promo{left:145px;top:455px;width:420px;height:50px;border:2px solid var(--line);border-radius:26px;display:flex;align-items:center;justify-content:space-between;padding:0 4px 0 33px;font-size:14px;color:#6d7380}
.promo-code{width:124px;height:40px;border-radius:20px;background:var(--teal);color:var(--white);font-weight:700;font-size:20px;display:flex;align-items:center;justify-content:center;letter-spacing:1px}
.dots{left:146px;top:573px;display:flex;gap:9px}
.dots span{width:11px;height:11px;border-radius:50%;background:#d6d9de}
.dots span.on{background:var(--navy)}
.hero-art{left:600px;top:120px}

/* about */
.about-art{left:78px;top:735px}
.section-title{font-size:46px;font-weight:500;color:var(--navy)}
.section-title .accent{color:var(--teal)}
.about-title{left:590px;top:780px}
.about-copy{left:591px;top:862px;width:480px;font-size:15.5px;line-height:32px}
.btn-more{height:42px;width:171px;background:var(--navy);font-size:15px}
.about-btn{left:591px;top:1089px}
.arrow-dot{width:14px;height:14px;border-radius:50%;background:var(--white);display:inline-flex;align-items:center;justify-content:center}

/* targets */
.band{left:0;top:1290px;width:1200px;height:595px;background:var(--grey-band)}
.band-wave{left:0;top:1270px}
.targets-title{left:0;top:1465px;width:1200px;text-align:center}
.cards{left:145px;top:1586px;display:flex;gap:17px}
.card{width:215px;height:178px;border-radius:4px;display:flex;flex-direction:column;align-items:center;justify-content:flex-start;padding-top:24px;color:var(--white);font-weight:500;font-size:16px;text-align:center;line-height:22px}
.card svg{margin-bottom:12px}
.card.teal{background:var(--teal)}
.card.navy{background:var(--navy)}
.round-arrow{width:44px;height:44px;border-radius:50%;border:2px solid #9ba1ab;background:var(--white);display:flex;align-items:center;justify-content:center}
.arrow-left{left:72px;top:1652px}
.arrow-right{left:1082px;top:1652px}

/* sustainable */
.sus-title{left:141px;top:2005px;font-size:48px;font-weight:500;line-height:54px;color:var(--navy)}
.sus-title .accent{color:var(--teal)}
.sus-copy{left:143px;top:2138px;width:500px;font-size:15.5px;line-height:32px}
.sus-btn{left:143px;top:2338px}
.sus-art{left:655px;top:1972px}

/* features */
.feature{width:240px;text-align:center;font-size:24px;font-weight:500;color:var(--ink)}
.feature svg{display:block;margin:0 auto 14px}
.btn-view{left:515px;top:2880px;width:170px;height:42px;background:var(--navy)}
.divider{left:20px;top:3025px;width:1160px;height:1px;background:var(--line)}

/* testimonial */
.avatar{left:158px;top:3137px}
.quote-open{left:340px;top:3120px;font-size:90px;font-family:Georgia,serif;color:#b9d8d8;line-height:1}
.quote-close{left:900px;top:3225px;font-size:90px;font-family:Georgia,serif;color:#b9d8d8;line-height:1}
.testimonial{left:412px;top:3132px;width:620px;font-size:16px;line-height:30px}
.cite{left:412px;top:3243px;font-size:14.5px;line-height:23px;font-weight:600;color:var(--ink)}
.chev{width:30px;height:40px}
.chev-left{left:80px;top:3186px}
.chev-right{left:1090px;top:3186px}

/* footer */
.footer{left:0;top:3397px;width:1200px;height:257px;background:var(--navy);border-top:4px solid var(--teal)}
.socials{left:478px;top:3456px;display:flex;gap:14px}
.socials span{width:50px;height:50px;border-radius:50%;border:2px solid var(--white);color:var(--white);display:flex;align-items:center;justify-content:center;font-size:14px;font-weight:600}
.footer-nav{left:0;top:3541px;width:1200px;text-align:center;font-size:19px;font-weight:500;color:var(--white);letter-spacing:.3px}
.footer-nav span.sep{margin:0 18px}
.copyright{left:0;top:3599px;width:1200px;text-align:center;font-size:14px;color:var(--white)}
</style>
</head>
<body>
<div class="abs top-rule"></div>

<header>
  <div class="abs brand"><span class="brand-mark"></span><span class="brand-name">TAPLEDGER</span></div>
  <nav class="abs nav"><a class="active" href="#">HOME</a><a href="#">ABOUT</a><a href="#">SERVICES</a></nav>
  <a class="abs btn btn-signup" href="#">SIGN UP</a>
  <a class="abs btn btn-check" href="#">CHECK AVAILABILITY</a>
</header>

<section class="hero">
  <h1 class="abs hero-title">TAPLEDGER</h1>
  <p class="abs hero-copy">Lorem ipsum dolor sit amonsectetur adipiscing<br>elit, sed do eiusmod tempor incididunt ut<br>labore et dolore magna aliqua.</p>
  <div class="abs promo"><span>Enter Promo code</span><span class="promo-code">RGWF3</span></div>
  <div class="abs dots"><span></span><span></span><span class="on"></span><span></span><span></span></div>
  <svg class="abs hero-art" width="600" height="560" viewBox="600 120 600 560">
    <defs>
      <linearGradient id="heroFill" x1="0" y1="0" x2="1" y2="1">
        <stop offset="0" stop-color="#b9b2a8"/><stop offset=".5" stop-color="#6f7d62"/><stop offset="1" stop-color="#3f4f3c"/>
      </linearGradient>
    </defs>
    <path role="img" aria-label="Photo of a smiling woman with glasses looking at her smartphone" fill="url(#heroFill)" d="M700 190 C790 140 1010 120 1200 128 L1200 640 C1120 590 1060 520 960 528 C860 536 700 590 632 470 C592 390 600 250 700 190 Z"/>
    <path fill="none" stroke="var(--teal-bright)" stroke-width="10" d="M616 420 C640 560 820 565 960 532 C1080 505 1130 610 1200 665"/>
  </svg>
</section>

<section class="about">
  <svg class="abs about-art" width="460" height="450" viewBox="0 0 460 450">
    <defs>
      <linearGradient id="aboutFill" x1="0" y1="0" x2="1" y2="1">
        <stop offset="0" stop-color="#2d2f34"/><stop offset=".55" stop-color="#6d6a68"/><stop offset="1" stop-color="#2f8fe0"/>
      </linearGradient>
    </defs>
    <circle role="img" aria-label="Photo of a hand holding a smartphone showing a digital business card" cx="228" cy="222" r="212" fill="url(#aboutFill)"/>
    <path fill="none" stroke="var(--teal)" stroke-width="8" d="M228 6 A216 216 0 0 0 228 438"/>
  </svg>
  <h2 class="abs section-title about-title">ABOUT <span class="accent">TAPLEDGER</span></h2>
  <p class="abs about-copy">90% of the worlds 10 Billion business cards, are thrown away<br>with 7 days. What a waste of paper and money!<br>'Virtual Business Card' or 'TapLedger' is the Digital Solution.<br>TapLedger is the intelligent, relevant and easy way for your new<br>customers or friends to receive ALL of your contact card<br>information and in to a few clicks, be saved to their phones.</p>
  <a class="abs btn btn-more about-btn" href="#">READ MORE <span class="arrow-dot"><svg width="8" height="8" viewBox="0 0 8 8"><path d="M3 1.5 5.5 4 3 6.5" fill="none" stroke="var(--navy)" stroke-width="1.6"/></svg></span></a>
</section>

<section class="targets">
  <div class="abs band"></div>
  <svg class="abs band-wave" width="1200" height="120" viewBox="0 0 1200 120">
    <path fill="var(--grey-band)" d="M0 60 C150 20 300 10 450 50 C600 85 700 10 850 20 C1000 30 1100 60 1200 40 L1200 120 L0 120 Z"/>
    <path fill="#e2e5ea" d="M90 62 C200 30 330 35 430 70 C330 92 200 90 90 62 Z"/>
    <path fill="#e2e5ea" d="M1065 55 C1110 40 1160 35 1200 38 L1200 78 C1150 70 1100 65 1065 55 Z"/>
  </svg>
  <h2 class="abs section-title targets-title">OUR <span class="accent">TARGETS ARE</span></h2>
  <div class="abs round-arrow arrow-left"><svg width="12" height="16" viewBox="0 0 12 16"><path d="M9 2 3 8l6 6" fill="none" stroke="var(--ink)" stroke-width="2"/></svg></div>
  <div class="abs cards">
    <div class="card teal">
      <svg width="70" height="62" viewBox="0 0 70 62" fill="none" stroke="#fff" stroke-width="2"><path d="M8 34 28 18 38 26 62 4M52 4h10v10"/><rect x="30" y="34" width="8" height="22"/><rect x="42" y="28" width="8" height="28"/><rect x="54" y="20" width="8" height="36"/><circle cx="16" cy="46" r="10"/><path d="M16 40v12M13 43h5M13 49h5"/></svg>
      TRADESPERSON</div>
    <div class="card navy">
      <svg width="70" height="66" viewBox="0 0 70 66" fill="none" stroke="#fff" stroke-width="2"><rect x="26" y="4" width="30" height="44"/><path d="M32 12h6M44 12h6M32 20h6M44 20h6M32 28h6M44 28h6M32 36h6M44 36h6"/><path d="M6 50c10-6 20-6 28 0h14c4 0 4 6 0 6H30M6 58c14 4 30 6 56-6"/></svg>
      REAL ESTATE<br>AGENTS</div>
    <div class="card teal">
      <svg width="72" height="66" viewBox="0 0 72 66" fill="none" stroke="#fff" stroke-width="2"><rect x="4" y="2" width="22" height="14" rx="2"/><path d="M9 8h12"/><circle cx="50" cy="14" r="8"/><path d="M36 60V38c0-8 6-12 14-12s14 4 14 12v22"/><circle cx="20" cy="32" r="7"/><path d="M8 60V48c0-6 5-9 12-9s12 3 12 9v12"/></svg>
      CONSULTANTS</div>
    <div class="card navy">
      <svg width="72" height="66" viewBox="0 0 72 66" fill="none" stroke="#fff" stroke-width="2"><circle cx="26" cy="16" r="9"/><path d="M8 62V44c0-9 8-14 18-14s18 5 18 14v18"/><rect x="44" y="30" width="22" height="28"/><circle cx="55" cy="44" r="5"/></svg>
      BANKERS</div>
  </div>
  <div class="abs round-arrow arrow-right"><svg width="12" height="16" viewBox="0 0 12 16"><path d="M3 2l6 6-6 6" fill="none" stroke="var(--ink)" stroke-width="2"/></svg></div>
</section>

<section class="sustainable">
  <h2 class="abs sus-title">0% PAPER,<br><span class="accent">100% SUSTAINABLE.</span></h2>
  <p class="abs sus-copy">Lorem ipsum dolor sit amet, consectetur adipiscing elit, sed do<br>eiusmod tempor incididunt ut labore et dolore magna aliqua.<br>Quis ipsum suspendisse ultricisus commodo viverra maecenas<br>accumsan lacus vel faciliem ipsum dolor sit amet, consectetur<br>adipiscing elit, sed do eiusmod tempor</p>
  <a class="abs btn btn-more sus-btn" href="#">READ MORE <span class="arrow-dot"><svg width="8" height="8" viewBox="0 0 8 8"><path d="M3 1.5 5.5 4 3 6.5" fill="none" stroke="var(--navy)" stroke-width="1.6"/></svg></span></a>
  <svg class="abs sus-art" width="460" height="460" viewBox="0 0 460 460">
    <defs>
      <linearGradient id="susFill" x1="0" y1="0" x2="1" y2="1">
        <stop offset="0" stop-color="#2a3148"/><stop offset=".5" stop-color="#a9bfd6"/><stop offset="1" stop-color="#e8eef4"/>
      </linearGradient>
    </defs>
    <circle role="img" aria-label="Photo of a businesswoman using her phone while holding documents" cx="222" cy="226" r="210" fill="url(#susFill)"/>
    <path fill="none" stroke="var(--teal)" stroke-width="8" d="M230 6 A218 218 0 0 1 230 442"/>
  </svg>
</section>

<section class="features">
  <div class="abs feature" style="left:80px;top:2505px">
    <svg width="60" height="58" viewBox="0 0 60 58" fill="none" stroke="var(--teal)" stroke-width="2"><circle cx="38" cy="36" r="10"/><circle cx="38" cy="36" r="4"/><rect x="6" y="30" width="18" height="22"/><path d="M10 36h10M10 42h10"/><rect x="26" y="4" width="18" height="12" rx="2"/><path d="M20 22c4-4 8-6 12-6"/></svg>
    Logical</div>
  <div class="abs feature" style="left:321px;top:2505px">
    <svg width="60" height="58" viewBox="0 0 60 58" fill="none" stroke="var(--teal)" stroke-width="2"><rect x="6" y="16" width="48" height="34" rx="3"/><path d="M22 16v-6h16v6M6 30h48"/><rect x="26" y="26" width="8" height="8"/></svg>
    Professional</div>
  <div class="abs feature" style="left:560px;top:2505px">
    <svg width="60" height="58" viewBox="0 0 60 58" fill="none" stroke="var(--teal)" stroke-width="2"><path d="M32 4 46 9v10c0 9-6 15-14 18-8-3-14-9-14-18V9z"/><path d="M26 20l5 5 8-9"/><path d="M4 44h10l10-4h12c3 0 3 5 0 5H24M14 52h20l18-10"/></svg>
    Data Safe</div>
  <div class="abs feature" style="left:824px;top:2505px">
    <svg width="60" height="58" viewBox="0 0 60 58" fill="none" stroke="var(--teal)" stroke-width="2"><rect x="6" y="6" width="40" height="26" rx="3"/><path d="M6 14h40M12 22h12"/><path d="M34 32l8 8v14h12V36l-10-8"/></svg>
    Secure Payment</div>

  <div class="abs feature" style="left:112px;top:2695px">
    <svg width="60" height="58" viewBox="0 0 60 58" fill="none" stroke="var(--teal)" stroke-width="2"><path d="M30 4c5 6 6 10 0 14-6-4-5-8 0-14z"/><path d="M4 24c8 0 14 6 26 18 12-12 18-18 26-18M30 42v12M12 30l8 16M48 30l-8 16"/></svg>
    Environment</div>
  <div class="abs feature" style="left:321px;top:2695px">
    <svg width="60" height="58" viewBox="0 0 60 58" fill="none" stroke="var(--teal)" stroke-width="2"><rect x="10" y="16" width="40" height="34" rx="2"/><path d="M22 6h28v10M16 26h14v14H16zM36 30h8M36 36h8"/></svg>
    Ease</div>
  <div class="abs feature" style="left:560px;top:2695px">
    <svg width="60" height="58" viewBox="0 0 60 58" fill="none" stroke="var(--teal)" stroke-width="2"><path d="M8 40l14-14 8 8 20-22M42 12h8v8"/><path d="M4 52c6-4 10-4 16-4h12c6 0 8-6 2-6"/><rect x="36" y="30" width="6" height="16"/><rect x="46" y="24" width="6" height="22"/></svg>
    Sales</div>
  <div class="abs feature" style="left:824px;top:2695px">
    <svg width="64" height="58" viewBox="0 0 64 58" fill="none" stroke="var(--teal)" stroke-width="2"><circle cx="28" cy="28" r="12"/><path d="M28 20v16M24 24h7M24 32h7"/><circle cx="50" cy="12" r="8"/><path d="M6 50h12l8-4h14M8 20v18"/></svg>
    Cost</div>

  <a class="abs btn btn-view" href="#">VIEW MORE <span class="arrow-dot"><svg width="8" height="8" viewBox="0 0 8 8"><path d="M3 1.5 5.5 4 3 6.5" fill="none" stroke="var(--navy)" stroke-width="1.6"/></svg></span></a>
  <div class="abs divider"></div>
</section>

<section class="testimonials">
  <svg class="abs chev chev-left" viewBox="0 0 30 40"><path d="M22 4 8 20l14 16" fill="none" stroke="#8a9099" stroke-width="3"/></svg>
  <svg class="abs avatar" width="176" height="176" viewBox="0 0 176 176">
    <defs><linearGradient id="avFill" x1="0" y1="0" x2="1" y2="1"><stop offset="0" stop-color="#d9dde2"/><stop offset="1" stop-color="#5f7fa6"/></linearGradient></defs>
    <circle cx="88" cy="88" r="84" fill="none" stroke="var(--teal)" stroke-width="5"/>
    <circle role="img" aria-label="Portrait of the customer giving the testimonial" cx="88" cy="88" r="76" fill="url(#avFill)"/>
  </svg>
  <div class="abs quote-open">“</div>
  <p class="abs testimonial">Sed ut perspiciatis unde omnis iste natus error sit voluptatem accusantium doloremque laudantium, totam rem aperiam, eaque ipsa quae ab illo inventore veritatis et quasi architecto beatae vitae dicta sunt explicabo.</p>
  <p class="abs cite">- John Doe<br>Lorem ipsum dolor sit amet</p>
  <div class="abs quote-close">”</div>
  <svg class="abs chev chev-right" viewBox="0 0 30 40"><path d="M8 4l14 16L8 36" fill="none" stroke="#8a9099" stroke-width="3"/></svg>
</section>

<footer>
  <div class="abs footer"></div>
  <div class="abs socials"><span aria-label="Chatterbook">CB</span><span aria-label="Chirpline">CL</span><span aria-label="ClipStream">CS</span><span aria-label="Workweb">WW</span></div>
  <p class="abs footer-nav">HOME<span class="sep">/</span>ABOUT<span class="sep">/</span>SERVICES<span class="sep">/</span>TERMS AND SERVICE<span class="sep">/</span>PRIVACY POLICY</p>
  <p class="abs copyright">© 2020 TapLedger . All Rights Reserved &nbsp;|&nbsp; Privacy Policy</p>
</footer>
</body>
</html>
```